New Business Card Design Project LORVANTI-Italy

we are LORVANTI-Italy
our company in the market for 3 years we are luxury cosmetic company and its about time for a facelift :)
i will like to have elegant luxurious and unique business card
that will give the person that get it a unique, luxurious and elegant impression
I'm VERY OPEN FOR NEW IDEAS , even duo i add a few files of things that i see on line and i like them

i add my logo as well
my website is LORVANTI.COM
(if you would like to see the main style that we have)

Target Market(s)

adult that have money :)

Industry/Entity Type

Business

Contact Information for Business Card

Name - Dario Lorvanti
Position - CEO and CO Founder
address - 4817 E Halvern
telephone - 555-384-1926
email - dario@lorvanti.com
fax - 555-384-1926
website - LORVANTI.COM

Colors
000000
959595
fbee3e
ffffff

Requirements
Must have
• big logo in GOLD color
• elegant look
• impressive
Nice to have
• not must but maybe classy pattern background
• not must but maybe emblem
• maybe clear plastic business card
Should not have
• colors
• images

```html
<!DOCTYPE html>
<html lang="en">
<head>
<meta charset="utf-8">
<title>LORVANTI Italy – Business Card</title>
<link href="https://fonts.googleapis.com/css2?family=Roboto:wght@400;500&display=swap" rel="stylesheet">
<style>
  :root {
    --backdrop: #2b2b2b;
    --card-white: #f4f4f4;
    --card-grey: #757575;
    --gold: #d4ad45;
    --gold-light: #e6c463;
    --gold-deep: #c99d33;
    --ink: #3d3d3d;
    --divider: #b9b9b9;
    --white: #ffffff;
  }
  * { margin: 0; padding: 0; box-sizing: border-box; }
  html, body {
    width: 1200px; height: 960px; overflow: hidden;
    background: var(--backdrop);
    font-family: "Roboto", Arial, sans-serif;
  }
  .stage { position: relative; width: 1200px; height: 960px; }

  .card {
    position: absolute; width: 600px; height: 342px;
    border-radius: 18px; overflow: hidden;
    box-shadow: 0 6px 14px rgba(0,0,0,.45);
  }
  .card--front { left: 314px; top: 114px; background: var(--card-white); }
  .card--back  { left: 311px; top: 473px; background: var(--card-grey); }

  /* brand block on the front */
  .brand {
    position: absolute; left: 88px; top: 70px; width: 190px;
    display: flex; flex-direction: column; align-items: center;
    color: var(--gold);
  }
  .brand__dot {
    width: 84px; height: 84px; border-radius: 50%;
    border: 3px solid var(--gold);
  }
  .brand__name {
    margin-top: 22px; font-size: 36px; font-weight: 400;
    letter-spacing: 1px; line-height: 1;
  }
  .brand__rule { width: 186px; height: 2px; background: var(--gold); margin-top: 9px; }
  .brand__place { margin-top: 8px; font-size: 13px; letter-spacing: 1px; }

  .divider {
    position: absolute; left: 308px; top: 68px; width: 1px; height: 178px;
    background: linear-gradient(to bottom, transparent, var(--divider), transparent);
  }

  /* contact block */
  .contact { position: absolute; left: 342px; top: 80px; color: var(--ink); }
  .contact__name { font-size: 22px; font-weight: 500; color: var(--gold); line-height: 1; }
  .contact__role { margin-top: 9px; font-size: 15.5px; }
  .contact__address { margin-top: 16px; font-size: 14px; }
  .contact__list { list-style: none; margin-top: 11px; font-size: 14px; }
  .contact__list li { display: flex; align-items: center; height: 23px; }
  .contact__list svg { width: 17px; height: 15px; margin-right: 7px; fill: var(--gold); }

  /* web band */
  .band {
    position: absolute; left: 0; top: 299px; width: 600px; height: 30px;
    background: linear-gradient(to right, var(--gold-deep), var(--gold-light) 55%, var(--gold) 82%, var(--card-grey) 82%);
  }
  .band__url {
    position: absolute; left: 0; width: 500px; top: 7px; text-align: center;
    color: var(--white); font-size: 15px; letter-spacing: 3.5px;
  }
  .band__seal {
    position: absolute; left: 482px; top: -3px; width: 36px; height: 36px;
    border-radius: 50%; background: var(--white); border: 3px solid var(--gold-light);
  }

  /* back side */
  .back-brand {
    position: absolute; left: 0; top: 78px; width: 600px;
    display: flex; flex-direction: column; align-items: center;
  }
  .back-brand__dot {
    width: 176px; height: 176px; border-radius: 50%;
    border: 5px solid var(--gold);
    display: flex; align-items: center; justify-content: center;
  }
  .back-brand__name { color: var(--gold); font-size: 28px; letter-spacing: 2px; }
  .back-url {
    position: absolute; left: 0; width: 600px; top: 288px; text-align: center;
    color: var(--white); font-size: 15px; letter-spacing: 3.5px;
  }
</style>
</head>
<body>
<main class="stage">

  <section class="card card--front" aria-label="Business card front">
    <div class="brand">
      <div class="brand__dot"></div>
      <div class="brand__name">LORVANTI</div>
      <div class="brand__rule"></div>
      <div class="brand__place">ITALY</div>
    </div>

    <div class="divider"></div>

    <div class="contact">
      <div class="contact__name">Dario Lorvanti</div>
      <div class="contact__role">CEO &amp; CO Founder</div>
      <div class="contact__address">4817 E Halvern</div>
      <ul class="contact__list">
        <li>
          <svg viewBox="0 0 24 24" aria-hidden="true"><path d="M6.6 10.8a15 15 0 0 0 6.6 6.6l2.2-2.2a1 1 0 0 1 1-.25 11.4 11.4 0 0 0 3.6.6 1 1 0 0 1 1 1V20a1 1 0 0 1-1 1A17 17 0 0 1 3 4a1 1 0 0 1 1-1h3.5a1 1 0 0 1 1 1c0 1.25.2 2.45.6 3.6a1 1 0 0 1-.25 1z"/></svg>
          555-384-1926
        </li>
        <li>
          <svg viewBox="0 0 24 24" aria-hidden="true"><path d="M7 2h8l3 3v5H7zM3 11h18a1 1 0 0 1 1 1v8H2v-8a1 1 0 0 1 1-1zm3 4v2h12v-2z"/></svg>
          555-384-1926
        </li>
        <li>
          <svg viewBox="0 0 24 24" aria-hidden="true"><path d="M2 5h20v14H2zm2 2v.5l8 5 8-5V7l-8 5z"/></svg>
          dario@lorvanti.com
        </li>
      </ul>
    </div>

    <div class="band">
      <div class="band__url">WWW.LORVANTI.COM</div>
      <div class="band__seal"></div>
    </div>
  </section>

  <section class="card card--back" aria-label="Business card back">
    <div class="back-brand">
      <div class="back-brand__dot">
        <span class="back-brand__name">LORVANTI</span>
      </div>
    </div>
    <div class="back-url">www.lorvanti.com</div>
  </section>

</main>
</body>
</html>
```